Corbell Lending Partners - Real estate loans - need a business card with a logo

I need a logo and a business card that looks elegant - that looks as if it is a big stablish corporation - We do real estate loans, my goal is to brand myself with colors black background - gold or silver letters - some combination - Name of the company different color than the rest of the card -

```html
<!DOCTYPE html>
<html lang="en">
<head>
<meta charset="utf-8">
<title>Corbell Lending Partners – Business Card</title>
<link href="https://fonts.googleapis.com/css2?family=Cinzel:wght@600&family=Arimo:wght@400&display=swap" rel="stylesheet">
<style>
  :root {
    --backdrop: #d6d3ce;
    --card: #0b0b0b;
    --gold: #d6a72e;
    --silver: #d9d9d9;
    --muted: #bdbdbd;
    --rule: #5a5a5a;
  }
  * { box-sizing: border-box; margin: 0; padding: 0; }
  html, body { width: 1200px; height: 935px; overflow: hidden; }
  body {
    background: var(--backdrop);
    position: relative;
    font-family: "Arimo", Arial, sans-serif;
  }
  .card {
    position: absolute;
    width: 520px;
    height: 298px;
    background: var(--card);
    border-radius: 3px;
  }
  .card--front { left: 70px; top: 130px; }
  .card--back { left: 610px; top: 490px; }

  .brand-name {
    font-family: "Cinzel", Georgia, serif;
    font-weight: 600;
    color: var(--gold);
    line-height: 1.05;
    letter-spacing: 0.04em;
  }
  .card--front .brand-name {
    position: absolute;
    left: 0; right: 0; top: 50%;
    transform: translateY(-50%);
    text-align: center;
    font-size: 34px;
  }
  .brand-name .sub { display: block; font-size: 0.5em; letter-spacing: 0.2em; }

  .card--back .brand-name {
    position: absolute;
    left: 34px; top: 112px;
    width: 200px;
    font-size: 24px;
  }
  .divider {
    position: absolute;
    left: 250px; top: 44px;
    width: 1px; height: 150px;
    background: var(--rule);
  }
  .contact {
    position: absolute;
    left: 268px; top: 44px;
  }
  .person-name {
    font-family: "Cinzel", Georgia, serif;
    font-weight: 600;
    color: var(--gold);
    font-size: 17px;
    letter-spacing: 0.03em;
  }
  .person-role { color: var(--muted); font-size: 12px; margin: 2px 0 14px; }
  .contact-list { list-style: none; }
  .contact-list li {
    display: flex; align-items: center; gap: 7px;
    color: var(--silver); font-size: 13px; margin-bottom: 6px;
  }
  .icon { width: 12px; height: 12px; flex: none; fill: var(--gold); }
  .address {
    position: absolute;
    left: 34px; bottom: 32px;
    display: flex; align-items: center; gap: 8px;
    color: var(--silver); font-size: 13px;
  }
  .address .icon { width: 12px; height: 15px; }
</style>
</head>
<body>

<section class="card card--front">
  <div class="brand-name">Corbell<span class="sub">Lending Partners</span></div>
</section>

<section class="card card--back">
  <div class="brand-name">Corbell<span class="sub">Lending Partners</span></div>
  <div class="divider"></div>
  <div class="contact">
    <p class="person-name">DANA WHITLOW</p>
    <p class="person-role">Director</p>
    <ul class="contact-list">
      <li><svg class="icon" viewBox="0 0 12 12"><path d="M2.5 1h2l1 2.7-1.3 1a6.5 6.5 0 0 0 3.1 3.1l1-1.3 2.7 1v2A1 1 0 0 1 10 11 9 9 0 0 1 1 2a1 1 0 0 1 1.5-1z"/></svg>949.555.0142</li>
      <li><svg class="icon" viewBox="0 0 12 12"><rect x="3" y="0.5" width="6" height="11" rx="1"/><rect x="4" y="2" width="4" height="7" fill="#0b0b0b"/></svg>949.555.0187</li>
      <li><svg class="icon" viewBox="0 0 12 12"><rect x="0.5" y="2" width="11" height="8" rx="1"/><path d="M1 2.6 6 6.5l5-3.9" fill="none" stroke="#0b0b0b" stroke-width="1.2"/></svg>info@corbelllending.com.au</li>
      <li><svg class="icon" viewBox="0 0 12 12"><circle cx="6" cy="6" r="5.5"/><path d="M0.5 6h11M6 0.5c-2.5 3-2.5 8 0 11M6 0.5c2.5 3 2.5 8 0 11" fill="none" stroke="#0b0b0b" stroke-width="0.9"/></svg>www.corbelllending.com.au</li>
    </ul>
  </div>
  <p class="address"><svg class="icon" viewBox="0 0 12 15"><path d="M6 0a5 5 0 0 0-5 5c0 3.8 5 10 5 10s5-6.2 5-10a5 5 0 0 0-5-5z"/><circle cx="6" cy="5" r="1.8" fill="#0b0b0b"/></svg>Delmar Avenue, Suite 410 Seaview, California 92655</p>
</section>

</body>
</html>
```